OBK Farcoast Logistics Limited

We need the buissnes card to be very exclusive. As we are all young in our company. We need this to be the gate to make our clients feel deep interest for us.

We are focused in as International Trade advisors, and our products go from Oil Tanker Ships to Rubber balls for dogs.

Our Slogan is Bringing Far Shores Near.
And our main marketing will be through Internet.

We were stablished in 2009 In Mexico and we also have offices in Hong Kong.
We have representatives in China and Europe.

Target Market(s)

Is every company or Individual that wants to develop an International Project or product development or Logistic service of Goods and people.
Some of our current projects are Ship Brokerage, Mine Brokerage, Real State and Product Pormotional development.

Industry/Entity Type

It Company

Requirements
Must have
• Our Logo and slogan, and make the card accoriding to the logo.
Nice to have
• Our Colors

```html
<!DOCTYPE html>
<html lang="en">
<head>
<meta charset="utf-8">
<title>OBK Farcoast Logistics Limited — Business Card</title>
<link rel="stylesheet" href="https://fonts.googleapis.com/css2?family=Open+Sans:wght@400;600;700&display=swap">
<style>
  :root {
    --stage: #e9e6e1;
    --paper: #ffffff;
    --band-blue: #1b7fbd;
    --rule-blue: #1f4fa3;
    --brand-green: #8cc63f;
    --slogan-blue: #2a55a8;
    --ink-grey: #3b3b3b;
    --on-band: #ffffff;
  }
  * { box-sizing: border-box; margin: 0; padding: 0; }
  html, body { width: 1200px; height: 720px; overflow: hidden; }
  body {
    background: var(--stage);
    font-family: "Open Sans", Arial, sans-serif;
    position: relative;
  }
  .card {
    position: absolute;
    top: 206px;
    width: 540px;
    height: 308px;
    background: var(--paper);
    box-shadow: 0 6px 18px rgba(0,0,0,0.18);
    overflow: hidden;
  }
  .card--front { left: 40px; }
  .card--back { left: 620px; }

  /* front */
  .front__brand {
    position: absolute;
    top: 28px; left: 0; width: 100%;
    text-align: center;
  }
  .brand-mark {
    display: inline-flex;
    align-items: center;
    gap: 10px;
  }
  .brand-dot {
    width: 22px; height: 22px; border-radius: 50%;
    background: var(--band-blue);
  }
  .brand-name {
    font-weight: 700;
    color: var(--brand-green);
    font-size: 54px;
    letter-spacing: 4px;
    line-height: 1;
  }
  .front__slogan {
    margin-top: 6px;
    color: var(--slogan-blue);
    font-size: 11px;
  }
  .front__rule {
    position: absolute;
    top: 154px; left: 0; width: 100%;
    height: 2px; background: var(--rule-blue);
  }
  .front__band {
    position: absolute;
    top: 160px; left: 0; width: 100%; height: 118px;
    background: var(--band-blue);
    color: var(--on-band);
    display: flex;
    align-items: center;
  }
  .holder {
    width: 262px;
    text-align: right;
    padding-right: 18px;
    line-height: 1.3;
  }
  .holder__name { font-size: 19px; font-weight: 700; }
  .holder__title { font-size: 14px; }
  .holder__address { font-size: 14px; margin-top: 4px; }
  .band__divider {
    width: 1px; height: 88px; background: rgba(255,255,255,0.8);
  }
  .contacts {
    list-style: none;
    padding-left: 14px;
    font-size: 14px;
    line-height: 1.5;
  }
  .contacts li { display: flex; align-items: center; gap: 8px; }
  .contacts svg { width: 13px; height: 13px; flex: none; }

  /* back */
  .back__brand {
    position: absolute;
    top: 70px; left: 0; width: 100%;
    text-align: center;
  }
  .back__brand .brand-name { font-size: 96px; letter-spacing: 6px; }
  .back__brand .brand-dot { width: 34px; height: 34px; }
  .back__slogan {
    position: absolute;
    top: 214px; left: 0; width: 100%;
    text-align: center;
    color: var(--slogan-blue);
    font-size: 21px;
  }
  .back__web {
    position: absolute;
    top: 248px; left: 0; width: 100%;
    text-align: center;
    color: var(--ink-grey);
    font-size: 19px;
    letter-spacing: 3px;
  }
</style>
</head>
<body>

<section class="card card--front" aria-label="Business card front">
  <div class="front__brand">
    <div class="brand-mark">
      <span class="brand-dot"></span>
      <span class="brand-name">OBK</span>
    </div>
    <p class="front__slogan">Bringing Far Shores Near</p>
  </div>
  <div class="front__rule"></div>
  <div class="front__band">
    <div class="holder">
      <p class="holder__name">Your Name</p>
      <p class="holder__title">Title</p>
      <p class="holder__address">Street Name, City Name<br>State Zip Code</p>
    </div>
    <div class="band__divider"></div>
    <ul class="contacts">
      <li>
        <svg viewBox="0 0 16 16" aria-hidden="true"><circle cx="8" cy="8" r="7.5" fill="#fff"/><path d="M5 4.5c.6-.4 1.1-.2 1.4.4l.6 1.2c.2.4 0 .8-.3 1l-.5.3c.4 1 1.2 1.8 2.2 2.3l.3-.5c.2-.4.6-.5 1-.3l1.2.6c.6.3.7.9.3 1.4-.7.9-1.6 1-2.6.5C6.6 10.3 5.2 8.9 4.6 7c-.3-1 0-1.8.4-2.5z" fill="#1b7fbd"/></svg>
        123-456-0789
      </li>
      <li>
        <svg viewBox="0 0 16 16" aria-hidden="true"><rect x="4" y="1" width="8" height="14" rx="1.5" fill="#fff"/><rect x="5.5" y="3" width="5" height="8" fill="#1b7fbd"/><circle cx="8" cy="13" r="0.9" fill="#1b7fbd"/></svg>
        123-456-0789
      </li>
      <li>
        <svg viewBox="0 0 16 16" aria-hidden="true"><rect x="1" y="3" width="14" height="10" rx="1.5" fill="#fff"/><path d="M1.5 4l6.5 5 6.5-5" fill="none" stroke="#1b7fbd" stroke-width="1.3"/></svg>
        info@farcoastlogistics.com
      </li>
      <li>
        <svg viewBox="0 0 16 16" aria-hidden="true"><circle cx="8" cy="8" r="7" fill="#fff"/><g fill="none" stroke="#1b7fbd" stroke-width="1"><circle cx="8" cy="8" r="5.5"/><ellipse cx="8" cy="8" rx="2.3" ry="5.5"/><path d="M2.5 8h11"/></g></svg>
        www.farcoastlogistics.com
      </li>
    </ul>
  </div>
</section>

<section class="card card--back" aria-label="Business card back">
  <div class="back__brand">
    <div class="brand-mark">
      <span class="brand-dot"></span>
      <span class="brand-name">OBK</span>
    </div>
  </div>
  <p class="back__slogan">Bringing Far Shores Near</p>
  <p class="back__web">www.farcoastlogistics.com</p>
</section>

</body>
</html>
```